we can communicate on this, but i want to follow the approach we took on Pellew|Marsh & Quinlan but i feel the card front needs the black background and the platinum and gold logo. The back? I am open. we can use the same info from PM&Q. Velmont Arc is an enhanced equity investment fund - basically a very exclusive boutique hedge fund that uses only stock options. very advanced things. hope you are interested

Contact Information for Business Card

Dr. Lewis T. Brennick, CFA
Scientifique de fusée financière
701.555.0143
LTBquant47@mailvantor.com

4718 Willow Creek Bend W.
West Fargo, ND 58078

No web site

Colors

Designer to choose colors to be used in the design.

Requirements
Nice to have
• I tend to prefer the most visible applications of the logo to include logo and name, the logo version with a black background and the gold and platinum components separated by the black. I see this working well for a single side (logo and name - this is card front to me).
• I am fairly open to other treatments on the reverse side with the data. To me, it makes sense to have a different color rendition of the logo on the reverse and it may be a muted black tone on tone or an oversized portion that would have spot UV. Or, the reverse may play with colors and layout
Should not have
• Other colors = no no
• Decorative font

```html
<!DOCTYPE html>
<html lang="en">
<head>
<meta charset="utf-8">
<title>Velmont Arc – Business Card</title>
<link href="https://fonts.googleapis.com/css2?family=Montserrat:wght@700&family=Open+Sans:wght@400;600;700&family=Roboto:wght@400&display=swap" rel="stylesheet">
<style>
  :root{
    --stage:#2b2b2d;
    --ink:#19191b;
    --gold:#c9a640;
    --paper:#ffffff;
    --text:#2a2a2a;
  }
  *{box-sizing:border-box;margin:0;padding:0}
  html,body{width:1200px;height:900px;overflow:hidden;background:var(--stage)}
  .canvas{position:relative;width:1200px;height:900px}

  .card{position:absolute;border-radius:22px;overflow:hidden}

  /* Front */
  .card-front{left:470px;top:60px;width:620px;height:354px;background:var(--ink);
    display:flex;flex-direction:column;align-items:center;justify-content:center;gap:22px}
  .brand-dot{width:96px;height:96px;border-radius:50%;background:var(--gold)}
  .brand-name{font-family:"Montserrat",sans-serif;font-weight:700;letter-spacing:3px;
    font-size:40px;color:var(--paper);white-space:nowrap}

  /* Back */
  .card-back{left:120px;top:460px;width:700px;height:400px;background:var(--paper)}
  .holder{position:absolute;left:52px;top:52px}
  .holder-name{font-family:"Open Sans",sans-serif;font-weight:700;font-size:24px;line-height:1.35;
    letter-spacing:1px;color:var(--gold);text-transform:uppercase;white-space:nowrap}
  .holder-title{font-family:"Open Sans",sans-serif;font-weight:600;font-size:19px;line-height:1.4;
    color:var(--ink);white-space:nowrap}
  .divider{position:absolute;left:52px;right:46px;top:130px;height:1.5px;background:var(--gold)}

  .contacts{position:absolute;left:52px;top:158px;list-style:none;
    font-family:"Roboto",sans-serif;font-size:18px;color:var(--text)}
  .contacts li{display:flex;align-items:center;gap:12px;height:34px;white-space:nowrap}
  .contacts svg{width:18px;height:18px;fill:var(--gold);flex:none}

  .back-brand{position:absolute;right:46px;top:150px;display:flex;flex-direction:column;align-items:center;gap:10px}
  .back-brand .brand-dot{width:70px;height:70px}
  .back-brand .brand-name{color:var(--ink);font-size:30px}

  .address{position:absolute;right:46px;bottom:52px;text-align:right;font-style:normal;
    font-family:"Roboto",sans-serif;font-size:18px;line-height:1.4;color:var(--text)}

  .footer-band{position:absolute;left:0;right:0;bottom:0;height:20px;display:flex}
  .footer-band .gold{width:62%;background:var(--gold)}
  .footer-band .gap{width:6px;background:var(--paper)}
  .footer-band .dark{flex:1;background:var(--ink)}
</style>
</head>
<body>
<main class="canvas">
  <section class="card card-front" aria-label="Card front">
    <span class="brand-dot" aria-hidden="true"></span>
    <span class="brand-name">VELMONT ARC</span>
  </section>

  <section class="card card-back" aria-label="Card back">
    <div class="holder">
      <p class="holder-name">Dr. Lewis T. Brennick, CFA</p>
      <p class="holder-title">Scientifique de fusée financière</p>
    </div>
    <div class="divider"></div>

    <ul class="contacts">
      <li>
        <svg viewBox="0 0 24 24" aria-hidden="true"><path d="M6.6 10.8a15.1 15.1 0 0 0 6.6 6.6l2.2-2.2a1 1 0 0 1 1-.25 11.4 11.4 0 0 0 3.6.57 1 1 0 0 1 1 1V20a1 1 0 0 1-1 1A17 17 0 0 1 3 4a1 1 0 0 1 1-1h3.5a1 1 0 0 1 1 1c0 1.25.2 2.45.57 3.57a1 1 0 0 1-.25 1z"/></svg>
        <span>701.555.0143</span>
      </li>
      <li>
        <svg viewBox="0 0 24 24" aria-hidden="true"><path d="M3 5h18a1 1 0 0 1 1 1v12a1 1 0 0 1-1 1H3a1 1 0 0 1-1-1V6a1 1 0 0 1 1-1zm1 2.2V17h16V7.2l-8 5.3z M5 7l7 4.6L19 7z"/></svg>
        <span>LTBquant47@mailvantor.com</span>
      </li>
    </ul>

    <div class="back-brand">
      <span class="brand-dot" aria-hidden="true"></span>
      <span class="brand-name">VELMONT ARC</span>
    </div>

    <address class="address">
      4718 Willow Creek Bend W.<br>
      West Fargo, ND 58078
    </address>

    <div class="footer-band" aria-hidden="true">
      <span class="gold"></span><span class="gap"></span><span class="dark"></span>
    </div>
  </section>
</main>
</body>
</html>
```